Tech business card design

We need an amazing business card design for our new business 'Pexla' a marketing tech startup based in Sydney, Australia. We provide an online marketplace for businesses to search and buy advertising media, connect with service providers and learn more about marketing. We wish to communicate 'cool tech', reliability and professionalism and design based around our logo.

Target Market(s)

Business Owners

Contact Information for Business Card

Name
Position
Email Address
Website
Phone Number

Font styles to use
Other font styles liked:
• Avenir & Avenir Next

Colors

Designer to choose colors to be used in the design.

```html
<!DOCTYPE html>
<html lang="en">
<head>
<meta charset="utf-8">
<title>Pexla Business Card</title>
<link rel="stylesheet" href="https://fonts.googleapis.com/css2?family=Source+Sans+3:wght@400;700;800&display=swap">
<style>
  :root {
    --backdrop: #9fcde2;
    --card-front: #ebecf1;
    --card-back: #ffffff;
    --ink: #10123a;
    --ink-soft: #1e2350;
    --rule: #253670;
    --text: #2a2d3a;
  }
  * { margin: 0; padding: 0; box-sizing: border-box; }
  html, body {
    width: 1149px; height: 1200px; overflow: hidden;
    background: var(--backdrop);
    font-family: "Source Sans 3", "Myriad Pro", Arial, sans-serif;
  }
  .canvas { position: relative; width: 1149px; height: 1200px; }
  .card {
    position: absolute; left: 118px; width: 914px; height: 523px;
    border-radius: 26px;
  }
  .card--front { top: 39px; background: var(--card-front); }
  .card--back { top: 638px; background: var(--card-back); }

  .wordmark {
    position: absolute; left: 0; right: 0; text-align: center;
    font-weight: 800; color: var(--ink);
    font-size: 176px; line-height: 1; letter-spacing: -0.01em;
  }
  .card--front .wordmark { top: 150px; }
  .card--back .wordmark { top: 62px; font-size: 160px; }

  .front-url {
    position: absolute; top: 437px; left: 0; right: 0; text-align: center;
    font-size: 30px; letter-spacing: 0.14em; color: var(--ink-soft);
  }

  .holder { position: absolute; top: 275px; left: 0; right: 0; text-align: center; }
  .holder__name { font-weight: 700; font-size: 31px; color: var(--ink-soft); line-height: 1.05; letter-spacing: 0.01em; }
  .holder__role { font-size: 27px; color: var(--ink); line-height: 1.15; }

  .divider {
    position: absolute; top: 360px; left: 46px; width: 819px; height: 5px;
    background: var(--rule);
  }

  .contacts { position: absolute; left: 46px; top: 382px; list-style: none; }
  .contacts li {
    display: flex; align-items: center; gap: 10px;
    font-size: 24px; color: var(--text); height: 35px;
  }
  .contacts li.web { letter-spacing: 0.12em; }
  .contacts svg { width: 23px; height: 23px; flex: none; }

  .address {
    position: absolute; right: 49px; top: 405px; text-align: right;
    font-size: 24px; line-height: 1.12; color: var(--text);
  }
</style>
</head>
<body>
<main class="canvas">
  <section class="card card--front">
    <div class="wordmark">pexla</div>
    <div class="front-url">www.pexla.com</div>
  </section>

  <section class="card card--back">
    <div class="wordmark">pexla</div>
    <div class="holder">
      <div class="holder__name">ALEX REED</div>
      <div class="holder__role">Position</div>
    </div>
    <div class="divider"></div>
    <ul class="contacts">
      <li>
        <svg viewBox="0 0 24 24" aria-hidden="true"><circle cx="12" cy="12" r="10.5" fill="none" stroke="#10123a" stroke-width="1.8"/><path d="M9 6.5c-1.5 1-2 3-1 5.5s3 4.6 5 5.5c1.6.6 2.6.2 3.2-.6l-2-2.2-1.6.8c-1.2-.6-2.4-2-3-3.4l1.2-1.2-1-3z" fill="#10123a"/></svg>
        012-345-6789
      </li>
      <li>
        <svg viewBox="0 0 24 24" aria-hidden="true"><rect x="1.5" y="5" width="21" height="14" fill="#10123a"/><path d="M2 5.5l10 7.5 10-7.5M2 18.5l7.5-6.5M22 18.5l-7.5-6.5" fill="none" stroke="#fff" stroke-width="1.6"/></svg>
        info@pexla.com
      </li>
      <li class="web">
        <svg viewBox="0 0 24 24" aria-hidden="true"><g fill="none" stroke="#10123a" stroke-width="1.6"><circle cx="12" cy="12" r="10"/><ellipse cx="12" cy="12" rx="4.5" ry="10"/><path d="M2 12h20M3.5 7h17M3.5 17h17M12 2v20"/></g></svg>
        www.pexla.com
      </li>
    </ul>
    <div class="address">Street name City Name,<br>Zipcode,012345</div>
  </section>
</main>
</body>
</html>
```